Brintel Works - Fast, Efficient and Gas Mainteance for Domestic, Commercial and Industrial clients

We are in the process of purchasing a new business and would like to get a new logo and business card.
Business is a gas maintenance business that also does new gas installations.
Has been established since 1988.
Services include:
Install all types of gas appliances & equipment inc. hot water units
Maintain / repair / replace all types of gas appliances & equipment

Target Market(s)

Domestic, Commercial and Industrial clients

Industry/Entity Type

Business

Contact Information for Business Card

admin@brintelworks.com.au
07 3918 4726
Brintel Works PTY LTD

Logo Text

Gas Fitting & Plumbing Maintenance Specialists

Font styles to use
Sans Serif

Requirements
Must have
• Logo
• Business name, contact number, email address, web address
• Domestic | Commercial | Industrial Est Since 1988
Nice to have
• Possibly a black card with a flame logo to one side
Should not have
• Spelling errors

```html
<!DOCTYPE html>
<html lang="en">
<head>
<meta charset="utf-8">
<title>Brintel Works – Business Card</title>
<link rel="stylesheet" href="https://fonts.googleapis.com/css2?family=Open+Sans:ital,wght@0,400;0,600;0,700;1,400&display=swap">
<style>
  :root {
    --backdrop: #e9e6e1;
    --card: #fbfbfb;
    --orange: #e2603d;
    --orange-deep: #cf4d31;
    --band-grey: #a9a9a9;
    --slate: #3e4350;
    --muted: #7d808a;
    --ink: #1d1d1f;
    --mark-light: #e6e6e8;
    --mark-dark: #c9c9cc;
  }
  * { box-sizing: border-box; margin: 0; padding: 0; }
  html, body { width: 1200px; height: 892px; overflow: hidden; }
  body {
    background: var(--backdrop);
    font-family: "Open Sans", Arial, sans-serif;
    position: relative;
  }
  .card {
    position: absolute;
    left: 260px;
    width: 680px;
    height: 388px;
    background: var(--card);
    box-shadow: 0 4px 14px rgba(0,0,0,0.12);
    overflow: hidden;
  }
  .card--front { top: 40px; }
  .card--back { top: 464px; }

  .logo-mark {
    position: absolute;
    border-radius: 50%;
    background: radial-gradient(circle at 50% 55%, var(--mark-dark), var(--mark-light) 70%, transparent 72%);
    opacity: 0.8;
  }
  .card--front .logo-mark { left: 28px; top: 70px; width: 112px; height: 112px; }
  .card--back .logo-mark { right: 70px; top: 36px; width: 130px; height: 130px; opacity: 0.6; }

  .brand { position: absolute; }
  .card--front .brand { left: 150px; top: 56px; }
  .card--back .brand { left: 70px; top: 180px; }
  .brand-name {
    font-weight: 700;
    font-size: 38px;
    color: var(--orange);
    text-transform: uppercase;
    letter-spacing: 0.5px;
    line-height: 1;
  }
  .brand-suffix {
    font-size: 9px;
    font-weight: 600;
    color: var(--slate);
    vertical-align: top;
    margin-left: 4px;
  }
  .brand-tagline {
    margin-top: 6px;
    font-size: 21px;
    font-weight: 600;
    color: var(--slate);
  }
  .brand-sectors {
    margin-top: 4px;
    font-size: 11px;
    color: var(--muted);
    letter-spacing: 0.3px;
  }
  .brand-sectors .est {
    margin-left: 14px;
    font-size: 14px;
    font-style: italic;
    color: #b3b4b9;
  }

  .contact {
    position: absolute;
    right: 26px;
    top: 158px;
    list-style: none;
    text-align: right;
  }
  .contact li {
    display: flex;
    justify-content: flex-end;
    align-items: center;
    gap: 14px;
    font-size: 18px;
    color: var(--ink);
    height: 30px;
  }
  .contact .icon {
    width: 16px;
    height: 16px;
    background: var(--ink);
    display: inline-flex;
    align-items: center;
    justify-content: center;
  }
  .band { position: absolute; left: 0; bottom: 0; width: 680px; height: 388px; }
</style>
</head>
<body>
  <section class="card card--front">
    <svg class="band" viewBox="0 0 680 388" aria-hidden="true">
      <defs>
        <linearGradient id="bandFill" x1="0" y1="0" x2="1" y2="0">
          <stop offset="0" stop-color="var(--orange)"/>
          <stop offset="1" stop-color="var(--orange-deep)"/>
        </linearGradient>
      </defs>
      <path d="M0 338 L250 338 C330 338 360 292 450 282 C540 272 610 266 680 262 L680 388 L0 388 Z" fill="var(--band-grey)"/>
      <path d="M0 352 L260 352 C340 352 370 306 460 296 C550 287 615 282 680 278 L680 388 L0 388 Z" fill="url(#bandFill)"/>
    </svg>

    <div class="logo-mark" role="img" aria-label="Brintel Works flame logo mark"></div>

    <div class="brand">
      <p class="brand-name">Brintel Works<span class="brand-suffix">PTY LTD</span></p>
      <p class="brand-tagline">Gas fitting &amp; Plumbing Specialists</p>
      <p class="brand-sectors">Domestic | Commercial | Industrial <span class="est">Est Since 1988</span></p>
    </div>

    <ul class="contact">
      <li>07 3918 4726
        <span class="icon"><svg width="10" height="10" viewBox="0 0 10 10" aria-hidden="true"><path d="M2 1 L4 1 L4.5 3 L3.3 3.8 C3.8 5 4.9 6.2 6.2 6.7 L7 5.5 L9 6 L9 8 C9 8.6 8.5 9 8 9 C4.2 8.8 1.2 5.8 1 2 C1 1.5 1.4 1 2 1 Z" fill="#fff"/></svg></span>
      </li>
      <li>admin@brintelworks.com.au
        <span class="icon"><svg width="10" height="8" viewBox="0 0 10 8" aria-hidden="true"><rect x="0.5" y="0.5" width="9" height="7" fill="none" stroke="#fff"/><path d="M0.5 0.5 L5 4.5 L9.5 0.5" fill="none" stroke="#fff"/></svg></span>
      </li>
      <li>www.brintelworks.com.au
        <span class="icon"><svg width="10" height="10" viewBox="0 0 10 10" aria-hidden="true"><circle cx="5" cy="5" r="4" fill="none" stroke="#fff"/><path d="M1 5 H9 M5 1 C3 3 3 7 5 9 M5 1 C7 3 7 7 5 9" fill="none" stroke="#fff" stroke-width="0.8"/></svg></span>
      </li>
    </ul>
  </section>

  <section class="card card--back">
    <div class="logo-mark" role="img" aria-label="Large faint Brintel Works flame logo mark"></div>
    <div class="brand">
      <p class="brand-name">Brintel Works<span class="brand-suffix">PTY LTD</span></p>
      <p class="brand-tagline">Gas fitting &amp; Plumbing Specialists</p>
      <p class="brand-sectors">Domestic | Commercial | Industrial <span class="est">Est Since 1988</span></p>
    </div>
  </section>
</body>
</html>
```